Website design with eCommerce for revolutionary new product in the manufacturing industry.

We need a website designed for a precision manufacturing company based in the suburbs of Minneapolis, Minnesota called Velkrin Manufacturing. We have a revolutionary new product, the TARN LOCK, to introduce and sell through an eCommerce storefront. The website would include company information, product information, and the storefront. Green is a color that represents Velkrin Manufacturing. The final design should communicate that we exclusively offer premium products at a premium price. The design should also let the customer know they are the focus of our work.

Target Market(s)

Machinists and machine shops

Industry/Entity Type

Manufacturing and machine shops

Coding

Coded - Design and coding required

Font styles to use
Sans Serif

Colors
59FF00
82FF00
B8FF75
E3FFCB
F4FFEA

Requirements
Must have
• eCommerce storefront, Made in USA references
Nice to have
• Home page, TARN LOCK Product page, About Us, Capabilities, Contact, etc.
Should not have
• Should not be too much text and reading.

```html
<!DOCTYPE html>
<html lang="en">
<head>
<meta charset="utf-8">
<title>Velkrin Manufacturing — Website Design</title>
<link rel="stylesheet" href="https://fonts.googleapis.com/css2?family=Poppins:ital,wght@0,400;0,500;0,600;0,700;0,800;1,600;1,700;1,800&display=swap">
<style>
:root{
  --green:#59ff00;
  --green-2:#82ff00;
  --green-soft:#b8ff75;
  --green-pale:#e3ffcb;
  --green-mist:#f4ffea;
  --ink:#111111;
  --black:#000000;
  --grey:#6d6d6d;
  --line:#e6e6e6;
  --board:#2b2b2b;
  --white:#ffffff;
}
*{box-sizing:border-box;margin:0;padding:0}
html,body{width:1200px;height:2754px;overflow:hidden}
body{background:var(--board);font-family:'Poppins',sans-serif;color:var(--ink);position:relative}

.board-brand{position:absolute;left:160px;top:292px;font-family:'Poppins',sans-serif;font-weight:800;font-size:62px;letter-spacing:2px;color:var(--white);line-height:1}

.page{position:absolute;width:440px;background:var(--white);overflow:hidden;box-shadow:0 20px 50px rgba(0,0,0,.55)}
.page-home{left:135px;top:445px;height:1831px}
.page-product{left:625px;top:126px;height:831px}
.page-gallery{left:625px;top:1005px;height:727px}
.page-contact{left:625px;top:1774px;height:853px}

/* nav */
.nav{position:absolute;top:10px;left:32px;right:32px;height:21px;background:var(--white);border-radius:3px;display:flex;align-items:center;padding:0 5px;z-index:5;box-shadow:0 2px 6px rgba(0,0,0,.2)}
.nav-brand{font-weight:800;font-size:8px;letter-spacing:.3px;color:var(--ink);margin-right:auto}
.nav-links{display:flex;gap:5px;list-style:none;align-items:center}
.nav-links li{font-size:3.6px;font-weight:600;color:var(--ink);white-space:nowrap}
.nav-links li.active{color:var(--green)}
.nav-links .nav-cta{background:var(--green);padding:3px 6px;border-radius:1px;color:var(--ink)}

/* hero */
.hero{position:absolute;left:0;top:0;width:440px}
.hero-shape{position:absolute;inset:0;width:100%;height:100%}
.hero-title{position:absolute;left:0;right:0;text-align:center;color:var(--white);font-style:italic;font-weight:800;text-transform:uppercase;line-height:1.05;text-shadow:0 2px 6px rgba(0,0,0,.4)}
.scroll-mouse{position:absolute;left:50%;width:6px;height:10px;margin-left:-3px;border:1px solid rgba(255,255,255,.8);border-radius:3px}
.scroll-mouse::after{content:"";position:absolute;left:1.5px;top:2px;width:1px;height:2px;background:#fff}

/* general */
.abs{position:absolute}
.section-title{position:absolute;left:0;right:0;text-align:center;font-style:italic;font-weight:800;font-size:15px;text-transform:uppercase;letter-spacing:.2px}
.section-sub{position:absolute;left:0;right:0;text-align:center;font-size:4.6px;color:var(--grey)}
.h-title{font-style:italic;font-weight:800;font-size:15px;line-height:1.05;text-transform:uppercase}
.body-text{font-size:4.6px;line-height:1.55;color:var(--grey)}
.ticks{list-style:none;margin-top:4px}
.ticks li{font-size:4.6px;line-height:1.6;color:var(--grey);padding-left:7px;position:relative}
.ticks li::before{content:"";position:absolute;left:0;top:2.4px;width:3px;height:3px;border-radius:50%;background:var(--green)}
.ticks li.sub{padding-left:16px}
.ticks li.sub::before{left:9px;background:none;border:.6px solid var(--green)}
.btn{display:inline-block;font-size:4.2px;font-weight:700;padding:3px 8px;border-radius:1px;text-transform:uppercase;transform:skewX(-12deg)}
.btn-dark{background:var(--black);color:var(--white)}
.btn-green{background:var(--green);color:var(--ink)}
.photo{position:absolute;border-radius:5px}

/* what we do */
.service-card{position:absolute;top:538px;width:120px;height:133px;background:var(--white);border-radius:4px;box-shadow:0 3px 10px rgba(0,0,0,.14);padding:12px 10px}
.service-card.featured{border:2px solid var(--green)}
.service-card svg{width:30px;height:26px;display:block;margin-bottom:6px}
.service-card p{font-size:4.4px;line-height:1.6;color:var(--grey)}

/* capabilities */
.cap-ring{position:absolute;left:163px;top:1064px;width:110px;height:110px;border-radius:50%;border:2px solid var(--green);border-left-color:#dcdcdc;border-top-color:#dcdcdc}
.cap-core{position:absolute;left:173px;top:1074px;width:90px;height:90px;border-radius:50%;background:var(--white);box-shadow:0 4px 14px rgba(0,0,0,.18);display:flex;align-items:center;justify-content:center;font-weight:800;font-size:11px}
.cap-item{position:absolute;width:108px}
.cap-item h4{font-style:italic;font-weight:800;font-size:5.6px;text-transform:uppercase}
.cap-item p{font-size:3.9px;line-height:1.45;color:var(--grey)}
.cap-left{left:30px;text-align:right}
.cap-right{left:290px}
.cap-dot{position:absolute;width:9px;height:9px;border:1px solid #555;border-radius:2px;background:var(--white)}
.cap-dot.on{background:var(--green);border-color:var(--green);border-radius:50%}

/* gallery tiles */
.tile{position:absolute;border-radius:4px}
.tile-green{background:var(--green);display:flex;align-items:center;justify-content:center;gap:4px}
.tile-green span{width:9px;height:9px;border-radius:50%;background:var(--white)}
.dots{position:absolute;left:0;right:0;display:flex;justify-content:center;gap:3px}
.dots i{width:4px;height:4px;border-radius:50%;background:#ccc}
.dots i.on{background:var(--green)}

/* newsletter */
.newsletter{position:absolute;left:36px;width:370px;height:54px;z-index:3}
.newsletter-bg{position:absolute;inset:0;background:var(--green);transform:skewX(-12deg);border-radius:4px}
.newsletter-title{position:absolute;left:24px;top:14px;font-style:italic;font-weight:800;font-size:15px;line-height:1}
.newsletter-sub{position:absolute;left:24px;top:30px;font-size:5px;color:var(--ink)}
.newsletter-form{position:absolute;right:18px;top:17px;width:198px;height:19px;display:flex;transform:skewX(-12deg)}
.newsletter-input{flex:1;background:var(--white);font-size:4.6px;color:#888;padding:6px 7px}
.newsletter-btn{width:64px;background:var(--black);color:var(--white);font-size:4.8px;font-weight:700;display:flex;align-items:center;justify-content:center}

/* footer */
.footer{position:absolute;left:0;width:440px;bottom:0;color:var(--white);z-index:2}
.footer-bg{position:absolute;inset:0;width:100%;height:100%}
.footer-brand{position:absolute;left:30px;top:112px;font-weight:800;font-size:13px;letter-spacing:.4px}
.footer-col{position:absolute;top:82px}
.footer-col h5{font-style:italic;font-weight:800;font-size:5px;margin-bottom:3px}
.footer-col li{list-style:none;font-size:3.9px;line-height:1.75;color:#cfcfcf}
.footer-col li b{display:inline-block;width:3px;height:3px;background:var(--green);border-radius:50%;margin-right:2px}
.footer-links{left:139px}
.footer-contact{left:223px}
.footer-map{position:absolute;left:225px;top:100px;width:90px;height:55px;background:radial-gradient(ellipse at center,#1c1c1c 0%,#0a0a0a 70%,transparent 100%);border-radius:8px}
.footer-social{position:absolute;left:314px;top:112px;display:flex;gap:5px}
.footer-social span{width:11px;height:11px;border-radius:50%;border:1px solid #555;background:#161616}
.footer-rule{position:absolute;left:32px;right:32px;bottom:22px;height:1px;background:#222}
.footer-copy{position:absolute;left:0;right:0;bottom:8px;text-align:center;font-size:4.4px;color:#ddd}
.footer-up{position:absolute;right:12px;bottom:14px;width:13px;height:13px;border-radius:50%;background:var(--green)}
.footer-up::after{content:"";position:absolute;left:4.5px;top:5px;width:3px;height:3px;border-left:1px solid #000;border-top:1px solid #000;transform:rotate(45deg)}

/* product + storefront */
.product-card{position:absolute;top:332px;width:118px;text-align:center}
.product-label{font-style:italic;font-weight:800;font-size:9px;line-height:1.1}
.product-buy{margin-top:3px;display:flex;align-items:center;justify-content:center;gap:6px}
.product-price{font-weight:700;font-size:7px;color:var(--ink)}
.product-cart{font-size:4.2px;font-weight:700;text-transform:uppercase;background:var(--green);color:var(--ink);padding:3px 7px;transform:skewX(-12deg)}
.usa-tag{display:inline-block;margin-top:6px;font-size:4.4px;font-weight:700;text-transform:uppercase;background:var(--green-pale);color:var(--ink);padding:2px 6px;border-radius:1px}

/* contact */
.contact-item{position:absolute;left:55px;display:flex;gap:12px;align-items:flex-start}
.contact-icon{width:18px;height:18px;background:var(--green);border-radius:2px;display:flex;align-items:center;justify-content:center}
.contact-icon svg{width:10px;height:10px}
.contact-label{font-size:7.4px;font-weight:600;color:var(--green);line-height:1.1}
.contact-value{font-size:7.6px;font-weight:600;color:var(--ink);line-height:1.2}
.form-card{position:absolute;left:224px;top:187px;width:150px;height:187px;background:var(--white);box-shadow:0 4px 16px rgba(0,0,0,.13);padding:14px 15px}
.form-card h3{font-style:italic;font-weight:800;font-size:11px;margin-bottom:8px}
.form-field{height:13px;background:#f2f2f2;font-size:3.8px;color:#777;padding:4px 6px;margin-bottom:4px}
.form-field.area{height:40px}
.form-submit{margin-top:8px;height:13px;background:var(--green);font-size:4.6px;font-weight:700;display:flex;align-items:center;justify-content:center;transform:skewX(-12deg)}
</style>
</head>
<body>

<div class="board-brand">TARN LOCK</div>

<!-- ============ HOME PAGE ============ -->
<section class="page page-home">
  <nav class="nav">
    <span class="nav-brand">TARN LOCK</span>
    <ul class="nav-links">
      <li>WHY VELKRIN?</li><li>WHAT WE DO</li><li>HOW WE MAKE IT BETTER</li><li>CAPABILITIES</li><li>GALLERY</li><li>ABOUT US</li><li>WISDOM</li><li class="nav-cta">CONTACT</li>
    </ul>
  </nav>
  <header class="hero" style="height:298px">
    <svg class="hero-shape" viewBox="0 0 440 100" preserveAspectRatio="none" role="img" aria-label="Close-up photo of blue-black steel coil springs">
      <defs><linearGradient id="heroHome" x1="0" y1="0" x2="1" y2="1"><stop offset="0" stop-color="#3a4654"/><stop offset=".5" stop-color="#26303c"/><stop offset="1" stop-color="#4c5b6c"/></linearGradient></defs>
      <path fill="url(#heroHome)" d="M0 0H440V78C440 93 430 100 395 100L0 81Z"/>
      <path fill="#59ff00" d="M0 81L395 100L0 95Z"/>
    </svg>
    <h1 class="hero-title" style="top:127px"><span style="font-size:15px;display:block">Welcome to Velkrin</span><span style="font-size:22px">Manufacturing</span></h1>
    <div class="scroll-mouse" style="top:253px"></div>
  </header>

  <div class="abs" style="left:28px;top:380px;width:72px;height:96px;border:2px solid var(--green);border-radius:3px"></div>
  <div class="photo" role="img" aria-label="Pile of shiny metal machining chips" style="left:40px;top:318px;width:157px;height:155px;background:linear-gradient(135deg,#8a8a8a,#3a3a3a 50%,#9d9d9d);box-shadow:0 4px 12px rgba(0,0,0,.3)"></div>
  <div class="abs" style="left:215px;top:369px;width:195px">
    <h2 class="h-title">Why Velkrin<br>Manufacturing?</h2>
    <p class="body-text" style="margin-top:5px">Because there is a better way, and we will find it, even if it is the harder way. We believe in working harder and smarter to achieve success.</p>
    <ul class="ticks">
      <li>Our success is measured in your success</li>
      <li>Focused on your needs and making parts right</li>
      <li>Exceeding your expectations</li>
    </ul>
  </div>

  <h2 class="section-title" style="top:510px">What we do</h2>
  <article class="service-card" style="left:31px">
    <svg viewBox="0 0 30 26" fill="none" stroke="#222" stroke-width="1"><circle cx="10" cy="10" r="5"/><circle cx="10" cy="10" r="2"/><rect x="4" y="18" width="22" height="6"/><circle cx="22" cy="8" r="3"/></svg>
    <p>We are a machine shop with complete end to end manufacturing ability. We can take an idea or need, bring it to a physical product, design and build your prototype, and we can mass produce it too.</p>
  </article>
  <article class="service-card featured" style="left:154px">
    <svg viewBox="0 0 30 26" fill="none" stroke="#222" stroke-width="1"><rect x="2" y="2" width="9" height="8"/><circle cx="24" cy="6" r="3"/><path d="M11 6H21"/><circle cx="7" cy="19" r="3"/><circle cx="22" cy="19" r="3"/><path d="M15 12L19 16" stroke="#59ff00"/></svg>
    <p>We love working directly with customers to make their products better where appropriate. We can work with as little as a verbal description, up to following fully defined customer specifications.</p>
  </article>
  <article class="service-card" style="left:277px">
    <svg viewBox="0 0 30 26" fill="none" stroke="#222" stroke-width="1"><rect x="4" y="2" width="22" height="6" rx="3"/><rect x="4" y="10" width="22" height="6" rx="3"/><rect x="4" y="18" width="22" height="6" rx="3"/><circle cx="8" cy="5" r="1.5" fill="#59ff00"/></svg>
    <p>We work in a wide variety of materials, and are very good at creating fixture designs to address your process issues. We can come to your business and help you make improvements onsite. We have helped many machine shops be more successful.</p>
  </article>

  <svg class="abs" style="left:0;top:713px" width="440" height="262" viewBox="0 0 440 262" preserveAspectRatio="none"><path fill="#59ff00" d="M0 30C0 8 15 0 40 3L440 42V228C420 202 392 200 362 210L0 262Z"/></svg>
  <div class="abs" style="left:33px;top:788px;width:178px">
    <h2 class="h-title">How we make<br>it better</h2>
    <ul class="ticks" style="margin-top:4px">
      <li style="color:#1c3a00">With 100 years of combined knowledge and experience to draw upon, we find solutions.</li>
      <li style="color:#1c3a00">Our vast experience across many industries gives us insight that is invaluable in creativity and foresight.</li>
      <li style="color:#1c3a00">This real life experience brings a broader understanding of what works, and more importantly, what does not, ultimately allowing us to make more informed decisions.</li>
    </ul>
    <span class="btn btn-dark" style="margin-top:7px">Read more</span>
  </div>
  <div class="photo" role="img" aria-label="Render of the green TARN LOCK stop tool with steel rod" style="left:225px;top:762px;width:175px;height:222px;background:linear-gradient(160deg,#3ec200,#1f7a00 60%,#8c8c8c);border-radius:10px;opacity:.9"></div>

  <h2 class="section-title" style="top:1012px">Capabilities</h2>
  <div class="cap-ring"></div>
  <div class="cap-core">TARN LOCK</div>
  <div class="cap-item cap-left" style="top:1052px"><h4>Capabilities</h4><p>While this list covers much of our work, it is by no means exhaustive.</p></div>
  <div class="cap-item cap-left" style="top:1082px"><h4>CAD Design</h4><p>Do you have something that needs to be created, but no method...</p></div>
  <div class="cap-item cap-left" style="top:1113px"><h4>CAM Programming</h4><p>Do you need programs for your machines? We can help.</p></div>
  <div class="cap-item cap-left" style="top:1145px"><h4>FFF 3D Printing</h4><p>Do you need a quick sample? Using fused filament printing...</p></div>
  <div class="cap-item cap-left" style="top:1177px"><h4>Prototypes</h4><p>Do you need a custom part, or test sample?</p></div>
  <div class="cap-item cap-right" style="top:1052px"><h4>Vertical CNC Machining</h4><p>With simultaneous 4th axis rotary if you need parts processed through...</p></div>
  <div class="cap-item cap-right" style="top:1082px"><h4>CNC Turning</h4><p>Collet or chuck work if you need parts processed through a CNC...</p></div>
  <div class="cap-item cap-right" style="top:1113px"><h4>Laser Marking</h4><p>Do you need a logo or other information permanently etched into your parts?</p></div>
  <div class="cap-item cap-right" style="top:1145px"><h4>Consulting and Appli...</h4><p>Do you need guidance with your own project?</p></div>
  <div class="cap-item cap-right" style="top:1177px"><h4>Manual Turning</h4><p>Good old fashioned skilled labor. Sometimes doing things the old way...</p></div>
  <span class="cap-dot" style="left:174px;top:1056px"></span>
  <span class="cap-dot" style="left:155px;top:1088px"></span>
  <span class="cap-dot" style="left:146px;top:1119px"></span>
  <span class="cap-dot" style="left:155px;top:1150px"></span>
  <span class="cap-dot" style="left:168px;top:1181px"></span>
  <span class="cap-dot" style="left:253px;top:1056px"></span>
  <span class="cap-dot" style="left:274px;top:1088px"></span>
  <span class="cap-dot on" style="left:281px;top:1119px"></span>
  <span class="cap-dot" style="left:274px;top:1150px"></span>
  <span class="cap-dot" style="left:261px;top:1181px"></span>

  <h2 class="section-title" style="top:1232px">Gallery</h2>
  <p class="section-sub" style="top:1252px">Here are some of the projects we've created over the years.</p>
  <div class="tile" role="img" aria-label="Rows of machined brass and steel parts" style="left:33px;top:1266px;width:92px;height:96px;background:linear-gradient(135deg,#a89a78,#595146)"></div>
  <div class="tile" role="img" aria-label="Polished machined metal part on dark background" style="left:130px;top:1266px;width:92px;height:96px;background:linear-gradient(135deg,#2a2a2a,#9a9a9a 50%,#333)"></div>
  <div class="tile tile-green" style="left:227px;top:1266px;width:90px;height:96px"><span></span><span></span></div>
  <div class="tile" role="img" aria-label="Perforated metal plate" style="left:322px;top:1266px;width:85px;height:96px;background:linear-gradient(135deg,#777,#3c3c3c)"></div>
  <div class="dots" style="top:1376px"><i class="on"></i><i></i><i></i></div>

  <div class="photo" role="img" aria-label="Machined brass fixtures on a blue mat" style="left:58px;top:1410px;width:149px;height:155px;background:linear-gradient(135deg,#2d4f8c,#1b2f57 55%,#b88a4c);box-shadow:0 4px 12px rgba(0,0,0,.3)"></div>
  <div class="abs" style="left:221px;top:1452px;width:180px">
    <h2 class="h-title">About us</h2>
    <p style="font-style:italic;font-weight:800;font-size:9.5px;margin-top:2px">VELKRIN MANUFACTURING</p>
    <p class="body-text" style="margin-top:4px">Velkrin Manufacturing has humble roots, starting as many machine shops do, in a home garage. The chance purchase of a CNC machining center started the journey, and the continued need for detailed solutions keeps it going and growing.</p>
    <div style="margin-top:6px;display:flex;gap:4px"><span class="btn btn-dark">Read more</span><span class="btn btn-green">Wisdom</span></div>
  </div>

  <div class="newsletter" style="top:1613px"><div class="newsletter-bg"></div><div class="newsletter-title">NEWSLETTER</div><div class="newsletter-sub">Subscribe to our newsletter</div><div class="newsletter-form"><div class="newsletter-input">Enter your email</div><div class="newsletter-btn">SUBSCRIBE</div></div></div>
  <footer class="footer" style="height:198px">
    <svg class="footer-bg" viewBox="0 0 440 198" preserveAspectRatio="none"><path fill="#000" d="M0 58L370 24C420 18 440 8 440 40V198H0Z"/></svg>
    <div class="footer-brand">TARN LOCK</div>
    <div class="footer-map"></div>
    <div class="footer-col footer-links"><h5>USEFUL LINKS</h5><ul><li>Why Velkrin?</li><li>What we do</li><li>How we make it better</li><li>Capabilities</li><li>About us</li><li>Gallery</li><li>Wisdom</li></ul></div>
    <div class="footer-col footer-contact"><h5>CONTACT US</h5><ul><li><b></b>Some goes address here</li><li><b></b>info@email.com</li><li><b></b>+92 1455 585</li><li><b></b>+92 1455 585</li></ul></div>
    <div class="footer-social"><span></span><span></span><span></span><span></span></div>
    <div class="footer-rule"></div>
    <div class="footer-copy">©Copyright 2022 | All Rights Reserved</div>
    <div class="footer-up"></div>
  </footer>
</section>

<!-- ============ PRODUCT PAGE ============ -->
<section class="page page-product">
  <nav class="nav">
    <span class="nav-brand">TARN LOCK</span>
    <ul class="nav-links"><li>WHY VELKRIN?</li><li>WHAT WE DO</li><li>HOW WE MAKE IT BETTER</li><li>CAPABILITIES</li><li>GALLERY</li><li>ABOUT US</li><li>WISDOM</li><li class="nav-cta">CONTACT</li></ul>
  </nav>
  <header class="hero" style="height:157px">
    <svg class="hero-shape" viewBox="0 0 440 100" preserveAspectRatio="none" role="img" aria-label="Dark photo of textured black machined parts">
      <defs><linearGradient id="heroProduct" x1="0" y1="0" x2="1" y2="1"><stop offset="0" stop-color="#2c2c2c"/><stop offset=".5" stop-color="#4a4a4a"/><stop offset="1" stop-color="#1e1e1e"/></linearGradient></defs>
      <path fill="url(#heroProduct)" d="M0 0H440V76C440 94 428 100 395 100L0 70Z"/>
      <path fill="#59ff00" d="M0 70L395 100L0 88Z"/>
    </svg>
    <h1 class="hero-title" style="top:60px;font-size:18px">Product</h1>
    <div class="scroll-mouse" style="top:100px"></div>
  </header>

  <div class="tile" role="img" aria-label="Green TLK-001 tool kit in foam case" style="left:32px;top:184px;width:118px;height:134px;background:linear-gradient(160deg,#4a4a4a,#2a2a2a 60%,#3ec200)"></div>
  <div class="tile" role="img" aria-label="Green TLK-002 tool kit in foam case" style="left:155px;top:184px;width:118px;height:134px;background:linear-gradient(160deg,#4a4a4a,#2a2a2a 60%,#3ec200)"></div>
  <div class="tile" role="img" aria-label="Green TLK-003 tool kit in foam case" style="left:278px;top:184px;width:128px;height:134px;background:linear-gradient(160deg,#4a4a4a,#2a2a2a 60%,#3ec200)"></div>
  <div class="product-card" style="left:32px"><div class="product-label">TLK-001</div><div class="product-buy"><span class="product-price">$349</span><span class="product-cart">Add to cart</span></div></div>
  <div class="product-card" style="left:155px"><div class="product-label">TLK-002</div><div class="product-buy"><span class="product-price">$389</span><span class="product-cart">Add to cart</span></div></div>
  <div class="product-card" style="left:283px"><div class="product-label">TLK-003</div><div class="product-buy"><span class="product-price">$429</span><span class="product-cart">Add to cart</span></div></div>

  <div class="photo" role="img" aria-label="Render of the green TARN LOCK stop tool" style="left:21px;top:378px;width:177px;height:203px;background:linear-gradient(160deg,#59ff00,#2f9900 55%,#c8c8c8)"></div>
  <div class="abs" style="left:219px;top:380px;width:195px">
    <h2 class="h-title">Product info</h2>
    <ul class="ticks" style="margin-top:3px">
      <li>Fastest and most reliable setups</li>
      <li>The locating stop rod is the highest point, so cutting clearance is no longer an issue</li>
      <li>The stop rod is top-loading</li>
      <li class="sub">No need to slide it the full length to replace it</li>
      <li>You can use a wide range of shapes and sizes of stop rods</li>
      <li class="sub">The end user can easily use almost any item at hand</li>
      <li>The clamping mechanisms do not require material deformation to function</li>
      <li>The adjustment fasteners are visible and easy to access for quick adjustments</li>
      <li>Only two fasteners are needed to access the full range of movements</li>
      <li>The arm can be rotated without changing the X-axis location</li>
      <li>The system can be mounted to many vises, the machine table or fixture surface</li>
      <li>The design is modular for easy customization or replacement</li>
      <li>Allows for use with very small or oddly shaped parts</li>
      <li>The materials and fasteners are common so maintenance is simple</li>
      <li>Made in USA</li>
    </ul>
    <span class="usa-tag">Made in USA · Secure checkout</span>
  </div>

  <div class="newsletter" style="top:611px;left:40px"><div class="newsletter-bg"></div><div class="newsletter-title">NEWSLETTER</div><div class="newsletter-sub">Subscribe to our newsletter</div><div class="newsletter-form"><div class="newsletter-input">Enter your email</div><div class="newsletter-btn">SUBSCRIBE</div></div></div>
  <footer class="footer" style="height:193px">
    <svg class="footer-bg" viewBox="0 0 440 193" preserveAspectRatio="none"><path fill="#000" d="M0 58L370 24C420 18 440 8 440 40V193H0Z"/></svg>
    <div class="footer-brand">TARN LOCK</div>
    <div class="footer-map"></div>
    <div class="footer-col footer-links"><h5>USEFUL LINKS</h5><ul><li>Why Velkrin?</li><li>What we do</li><li>How we make it better</li><li>Capabilities</li><li>About us</li><li>Gallery</li><li>Wisdom</li></ul></div>
    <div class="footer-col footer-contact"><h5>CONTACT US</h5><ul><li><b></b>Some goes address here</li><li><b></b>info@email.com</li><li><b></b>+92 1455 585</li><li><b></b>+92 1455 585</li></ul></div>
    <div class="footer-social"><span></span><span></span><span></span><span></span></div>
    <div class="footer-rule"></div>
    <div class="footer-copy">©Copyright 2022 | All Rights Reserved</div>
    <div class="footer-up"></div>
  </footer>
</section>

<!-- ============ GALLERY PAGE ============ -->
<section class="page page-gallery">
  <nav class="nav">
    <span class="nav-brand">TARN LOCK</span>
    <ul class="nav-links"><li>WHY VELKRIN?</li><li>WHAT WE DO</li><li>HOW WE MAKE IT BETTER</li><li>CAPABILITIES</li><li class="active">GALLERY</li><li>ABOUT US</li><li>WISDOM</li><li class="nav-cta">CONTACT</li></ul>
  </nav>
  <header class="hero" style="height:155px">
    <svg class="hero-shape" viewBox="0 0 440 100" preserveAspectRatio="none" role="img" aria-label="Dark photo of curled metal turnings">
      <defs><linearGradient id="heroGallery" x1="0" y1="0" x2="1" y2="1"><stop offset="0" stop-color="#2a2a2a"/><stop offset=".5" stop-color="#555"/><stop offset="1" stop-color="#262626"/></linearGradient></defs>
      <path fill="url(#heroGallery)" d="M0 0H440V76C440 94 428 100 395 100L0 70Z"/>
      <path fill="#59ff00" d="M0 70L395 100L0 88Z"/>
    </svg>
    <h1 class="hero-title" style="top:60px;font-size:18px">Gallery</h1>
    <div class="scroll-mouse" style="top:100px"></div>
  </header>

  <h2 class="section-title" style="top:191px">Our projects</h2>
  <p class="section-sub" style="top:211px">Here are some of the projects we've created over the years.</p>
  <div class="tile" role="img" aria-label="Rows of machined brass and steel parts" style="left:32px;top:224px;width:90px;height:97px;background:linear-gradient(135deg,#a89a78,#595146)"></div>
  <div class="tile" role="img" aria-label="Polished machined metal part" style="left:127px;top:224px;width:90px;height:97px;background:linear-gradient(135deg,#2a2a2a,#9a9a9a 50%,#333)"></div>
  <div class="tile tile-green" style="left:222px;top:224px;width:90px;height:97px"><span></span><span></span></div>
  <div class="tile" role="img" aria-label="Perforated metal plate" style="left:317px;top:224px;width:89px;height:97px;background:linear-gradient(135deg,#777,#3c3c3c)"></div>
  <div class="tile" role="img" aria-label="Machined aluminium grid surface" style="left:32px;top:331px;width:90px;height:96px;background:linear-gradient(135deg,#9a9a9a,#4c4c4c)"></div>
  <div class="tile" role="img" aria-label="Brass fixtures on a blue mat" style="left:127px;top:331px;width:90px;height:96px;background:linear-gradient(135deg,#2d4f8c,#b88a4c)"></div>
  <div class="tile" role="img" aria-label="Green TARN LOCK tool in foam case" style="left:222px;top:331px;width:90px;height:96px;background:linear-gradient(160deg,#4a4a4a,#2a2a2a 60%,#3ec200)"></div>
  <div class="tile" role="img" aria-label="Curled metal turnings" style="left:317px;top:331px;width:89px;height:96px;background:linear-gradient(135deg,#444,#8e8e8e 50%,#2a2a2a)"></div>
  <div class="abs" style="left:0;right:0;top:451px;text-align:center"><span class="btn btn-green">Load more</span></div>

  <div class="newsletter" style="top:507px;left:40px"><div class="newsletter-bg"></div><div class="newsletter-title">NEWSLETTER</div><div class="newsletter-sub">Subscribe to our newsletter</div><div class="newsletter-form"><div class="newsletter-input">Enter your email</div><div class="newsletter-btn">SUBSCRIBE</div></div></div>
  <footer class="footer" style="height:193px">
    <svg class="footer-bg" viewBox="0 0 440 193" preserveAspectRatio="none"><path fill="#000" d="M0 58L370 24C420 18 440 8 440 40V193H0Z"/></svg>
    <div class="footer-brand">TARN LOCK</div>
    <div class="footer-map"></div>
    <div class="footer-col footer-links"><h5>USEFUL LINKS</h5><ul><li>Why Velkrin?</li><li>What we do</li><li>How we make it better</li><li>Capabilities</li><li>About us</li><li>Gallery</li><li>Wisdom</li></ul></div>
    <div class="footer-col footer-contact"><h5>CONTACT US</h5><ul><li><b></b>Some goes address here</li><li><b></b>info@email.com</li><li><b></b>+92 1455 585</li><li><b></b>+92 1455 585</li></ul></div>
    <div class="footer-social"><span></span><span></span><span></span><span></span></div>
    <div class="footer-rule"></div>
    <div class="footer-copy">©Copyright 2022 | All Rights Reserved</div>
    <div class="footer-up"></div>
  </footer>
</section>

<!-- ============ CONTACT PAGE ============ -->
<section class="page page-contact">
  <nav class="nav">
    <span class="nav-brand">TARN LOCK</span>
    <ul class="nav-links"><li>WHY VELKRIN?</li><li>WHAT WE DO</li><li>HOW WE MAKE IT BETTER</li><li>CAPABILITIES</li><li>GALLERY</li><li>ABOUT US</li><li>WISDOM</li><li class="nav-cta">CONTACT</li></ul>
  </nav>
  <header class="hero" style="height:155px">
    <svg class="hero-shape" viewBox="0 0 440 100" preserveAspectRatio="none" role="img" aria-label="Photo of a heap of grey metal shavings">
      <defs><linearGradient id="heroContact" x1="0" y1="0" x2="1" y2="1"><stop offset="0" stop-color="#3a3a3a"/><stop offset=".5" stop-color="#6a6a6a"/><stop offset="1" stop-color="#2e2e2e"/></linearGradient></defs>
      <path fill="url(#heroContact)" d="M0 0H440V76C440 94 428 100 395 100L0 70Z"/>
      <path fill="#59ff00" d="M0 70L395 100L0 88Z"/>
    </svg>
    <h1 class="hero-title" style="top:60px;font-size:18px">Contact</h1>
    <div class="scroll-mouse" style="top:100px"></div>
  </header>

  <h2 class="h-title abs" style="left:55px;top:220px">Contact info</h2>
  <div class="contact-item" style="top:256px">
    <div class="contact-icon"><svg viewBox="0 0 10 10"><path fill="#000" d="M2 1L4 1L4.6 3.2L3.5 4C4 5.2 4.8 6 6 6.5L6.8 5.4L9 6V8C9 8.6 8.6 9 8 9C4.1 9 1 5.9 1 2C1 1.4 1.4 1 2 1Z"/></svg></div>
    <div><div class="contact-label">Phone :</div><div class="contact-value">555 0142 388</div></div>
  </div>
  <div class="contact-item" style="top:290px">
    <div class="contact-icon"><svg viewBox="0 0 10 10"><rect x="1" y="2" width="8" height="6" fill="#000"/><path d="M1 2L5 5.5L9 2" fill="none" stroke="#59ff00" stroke-width=".8"/></svg></div>
    <div><div class="contact-label">Email:</div><div class="contact-value">info@tarnlock.com</div></div>
  </div>
  <div class="contact-item" style="top:324px">
    <div class="contact-icon"><svg viewBox="0 0 10 10"><path fill="#000" d="M5 0.8C3.2 0.8 2 2.1 2 3.8C2 6 5 9.2 5 9.2S8 6 8 3.8C8 2.1 6.8 0.8 5 0.8Z"/><circle cx="5" cy="3.8" r="1.1" fill="#59ff00"/></svg></div>
    <div><div class="contact-label">Address :</div><div class="contact-value">Some goes address here</div></div>
  </div>

  <form class="form-card">
    <h3>GET IN TOUCH</h3>
    <div class="form-field">Name</div>
    <div class="form-field">Company Name</div>
    <div class="form-field">Phone Number</div>
    <div class="form-field">Email</div>
    <div class="form-field area">Message</div>
    <div class="form-submit">SUBMIT</div>
  </form>

  <div class="abs" role="img" aria-label="Street map showing the company location with a green pin" style="left:32px;top:411px;width:374px;height:192px;background:linear-gradient(135deg,#ededed,#dcdcdc 50%,#e8e8e8)"></div>

  <div class="newsletter" style="top:631px;left:40px"><div class="newsletter-bg"></div><div class="newsletter-title">NEWSLETTER</div><div class="newsletter-sub">Subscribe to our newsletter</div><div class="newsletter-form"><div class="newsletter-input">Enter your email</div><div class="newsletter-btn">SUBSCRIBE</div></div></div>
  <footer class="footer" style="height:193px">
    <svg class="footer-bg" viewBox="0 0 440 193" preserveAspectRatio="none"><path fill="#000" d="M0 58L370 24C420 18 440 8 440 40V193H0Z"/></svg>
    <div class="footer-brand">TARN LOCK</div>
    <div class="footer-map"></div>
    <div class="footer-col footer-links"><h5>USEFUL LINKS</h5><ul><li>Why Velkrin?</li><li>What we do</li><li>How we make it better</li><li>Capabilities</li><li>About us</li><li>Gallery</li><li>Wisdom</li></ul></div>
    <div class="footer-col footer-contact"><h5>CONTACT US</h5><ul><li><b></b>Some goes address here</li><li><b></b>info@email.com</li><li><b></b>+92 1455 585</li><li><b></b>+92 1455 585</li></ul></div>
    <div class="footer-social"><span></span><span></span><span></span><span></span></div>
    <div class="footer-rule"></div>
    <div class="footer-copy">©Copyright 2022 | All Rights Reserved</div>
    <div class="footer-up"></div>
  </footer>
</section>

</body>
</html>
```